A Modern & Sleek "Coming Soon" Page for an A.I Recruiting App

For the “Coming Soon” website, a simple background with no people in it. I've attached an A.I image of what the page should generally look like.

- A single mobile phone as the main focus where the user actually clicks on the, “notify me” button (after entering their email address).
- In the background where the pillars/columns are seen in the example, should be subtle pad locks that are in their opened position with a key inside the lock. I've attached images to try to illustrate this idea, but they are far away in style from what I'm looking for.

SLOGAN: Unlocking the power of meaningful connections
LOGO/TITLE: Should be the name as shown in image with only the name "KelvoLink" on it
COLORS: Purplish/blue hues. Should not be too feminine
NOTE: The user should only click once when signing up/entering their email.

Product: A recruiting platform that matches employers/employees with A.I. and prioritizing cultural fit/values system before skills. The industry we are tackling first is the caregiving industry (nannies, tutors, elderly). All users will be background screened and that info lives on the blockchain. All users will have the option to review and be reviewed/rated.

```html
<!DOCTYPE html>
<html lang="en">
<head>
<meta charset="utf-8">
<title>KelvoLink — Coming Soon</title>
<link rel="stylesheet" href="https://fonts.googleapis.com/css2?family=IBM+Plex+Sans:wght@400;600&family=Montserrat:wght@300&display=swap">
<style>
  :root {
    --bg-deep: #01060d;
    --bg-navy: #041427;
    --glow-blue: rgba(22, 86, 190, 0.45);
    --glow-teal: rgba(20, 140, 130, 0.28);
    --ink: #ffffff;
    --ink-dark: #0a0f1a;
    --phone-purple: #4a1f78;
    --phone-violet: #2a0f4a;
    --lock-cyan: #2aa9c8;
  }
  * { margin: 0; padding: 0; box-sizing: border-box; }
  html, body { width: 1200px; height: 825px; overflow: hidden; }
  body {
    position: relative;
    background:
      radial-gradient(ellipse 520px 260px at 560px 330px, var(--glow-teal), transparent 70%),
      radial-gradient(ellipse 700px 420px at 300px 260px, var(--glow-blue), transparent 70%),
      radial-gradient(ellipse 600px 300px at 1050px 680px, rgba(22, 86, 190, 0.3), transparent 70%),
      linear-gradient(180deg, var(--bg-deep), var(--bg-navy) 55%, var(--bg-deep));
    color: var(--ink);
    font-family: "IBM Plex Sans", sans-serif;
  }
  .site-header {
    position: absolute; left: 60px; right: 62px; top: 52px;
    display: flex; justify-content: space-between; align-items: center;
  }
  .brand-name {
    font-family: "Montserrat", sans-serif; font-weight: 300;
    font-size: 40px; letter-spacing: 6px; line-height: 36px; text-transform: uppercase;
  }
  .menu-toggle { width: 45px; height: 32px; display: block; }
  .hero-visual {
    position: absolute; left: 128px; top: 180px; width: 584px; height: 553px;
    border-radius: 28px;
    background:
      radial-gradient(ellipse 120px 110px at 470px 430px, rgba(42, 169, 200, 0.45), transparent 75%),
      radial-gradient(ellipse 200px 290px at 180px 270px, var(--phone-purple), transparent 80%),
      radial-gradient(ellipse 260px 320px at 200px 280px, var(--phone-violet), transparent 85%);
  }
  .hero-copy { position: absolute; left: 703px; top: 286px; }
  .hero-title {
    font-family: "Montserrat", sans-serif; font-weight: 300;
    font-size: 70px; letter-spacing: 5px; line-height: 84px;
  }
  .hero-tagline { margin-top: 22px; font-size: 19.5px; line-height: 26px; }
  .signup-button {
    display: inline-flex; align-items: center; justify-content: center;
    margin-top: 46px; width: 166px; height: 55px; border-radius: 28px;
    background: var(--ink); color: var(--ink-dark);
    font-weight: 600; font-size: 19px; text-decoration: none;
  }
</style>
</head>
<body>
  <header class="site-header">
    <div class="brand-name">KelvoLink</div>
    <svg class="menu-toggle" viewBox="0 0 45 32" aria-label="Menu" role="img">
      <g stroke="#ffffff" stroke-width="4" stroke-linecap="round">
        <line x1="8" y1="3" x2="43" y2="3"/>
        <line x1="2" y1="16" x2="43" y2="16"/>
        <line x1="18" y1="29" x2="43" y2="29"/>
      </g>
    </svg>
  </header>

  <div class="hero-visual" role="img" aria-label="Smartphone showing the app launch screen with a notify me button, beside an open cyan padlock with a key"></div>

  <main class="hero-copy">
    <h1 class="hero-title">KelvoLink</h1>
    <p class="hero-tagline">Unlocking the power of meaningful connections</p>
    <a class="signup-button" href="#">Sign Up</a>
  </main>
</body>
</html>
```